Cat-products company needs smart, yet endearing, business card

We need a business card design for a new, but up-and-running, business based in Honolulu, Hawaii. The business is Purrnest Nook Co. Our first product is the most environmentally-friendly cat grass kit ever seen on the planet. Future products, currently in the R&D phase, will include a variety of exciting cat scratchers. We also do consulting work to help apartment-dwellers make their home more cat-friendly and, in the future, plan on doing full, custom installs of structure to create high walkways for cats.

Target Market(s)

Middle-aged, apartment-dwelling, middle-class workers who own 1 or more cats and who dote on them.

Industry/Entity Type

Pet Care

Contact Information for Business Card

A striking, professional, yet warm and friendly design is what we're after.

Font styles to use
Serif
Sans Serif
Other font styles liked:
• Comfortaa

Colors

Designer to choose colors to be used in the design.

Requirements
Must have
• The company logo: (see attachment)
• The company name: Purrnest Nook Co
• The web address: www.purrnestnookco.com
• Email: support@purrnestnookco.com
• Phone: +1 (808) 571 6023
• Update (Fri Jun 30 3017 7:45pm Hawaii Time) I would like, is possible, uploaded picture of the cat grass kit on the back of the card with some text along the lines of: Purrnest Nook Co - Maker Of The Leafiest Feline Sprout Set Yet
Nice to have
• A cat picture, cartoon, real or silhouette that illustrates cats in action and/or relaxing; ie using the apartment space to live, play and relax in and being well-contented.
• Most of the website is done in the font: Comfortaa. It might be nice to continue using this for brand consistency.
Should not have
• Hard-to-read fonts.

```html
<!DOCTYPE html>
<html lang="en">
<head>
<meta charset="utf-8">
<title>Purrnest Nook Co — Business Card</title>
<link rel="stylesheet" href="https://fonts.googleapis.com/css2?family=Open+Sans:wght@400;600;700&display=swap">
<style>
  :root {
    --backdrop: #3b3431;
    --card: #141414;
    --card-edge: #1f1f1f;
    --emboss: #2a2a2a;
    --emboss-text: #3a3a3a;
    --ink: #f2f2f2;
    --muted: #8a8a8a;
    --brand-orange: #f5a623;
    --brand-brown: #6b4636;
    --rule: #5a3a2c;
    --social: #4a4a4a;
  }
  * { box-sizing: border-box; margin: 0; padding: 0; }
  html, body {
    width: 1200px; height: 864px; overflow: hidden;
    background: var(--backdrop);
    font-family: "Open Sans", Arial, sans-serif;
  }
  .stage {
    width: 1200px; height: 864px;
    display: flex; align-items: center; justify-content: center; gap: 40px;
  }
  .card {
    position: relative;
    width: 520px; height: 298px;
    background: var(--card);
    border: 1px solid var(--card-edge);
    box-shadow: 0 10px 24px rgba(0,0,0,.45);
  }

  /* Front */
  .card-front .social {
    position: absolute; top: 22px; right: 24px;
    display: flex; gap: 5px;
  }
  .card-front .social span {
    width: 14px; height: 14px; border-radius: 50%; background: var(--social);
  }
  .card-front .wordmark {
    position: absolute; left: 0; right: 0; top: 100px;
    display: flex; align-items: center; justify-content: center; gap: 12px;
  }
  .card-front .wordmark-square {
    width: 34px; height: 34px; background: var(--emboss);
  }
  .card-front .wordmark-name {
    font-weight: 700; font-size: 32px; color: var(--emboss-text);
    letter-spacing: .5px;
  }
  .card-front .site {
    position: absolute; left: 0; right: 0; top: 186px;
    text-align: center; font-size: 13px; letter-spacing: 4px;
    color: var(--muted);
  }

  /* Back */
  .card-back .person {
    position: absolute; left: 28px; top: 54px;
  }
  .card-back .person-name {
    font-size: 12px; font-weight: 600; letter-spacing: .5px;
    color: var(--brand-brown); text-transform: uppercase;
  }
  .card-back .person-role {
    font-size: 14px; color: var(--brand-orange); margin-top: 2px;
  }
  .card-back .contacts {
    position: absolute; left: 28px; top: 104px;
    list-style: none; font-size: 13px; color: var(--ink); line-height: 19px;
  }
  .card-back .contacts li { display: flex; align-items: center; gap: 8px; }
  .card-back .contacts svg { width: 10px; height: 10px; fill: var(--muted); flex: none; }
  .card-back .divider {
    position: absolute; left: 28px; right: 28px; top: 174px;
    height: 1px; background: var(--rule);
  }
  .card-back .wordmark {
    position: absolute; right: 28px; top: 116px;
    display: flex; align-items: center; gap: 8px;
  }
  .card-back .wordmark-dot {
    width: 22px; height: 22px; border-radius: 50%; background: var(--brand-brown);
  }
  .card-back .wordmark-name {
    font-size: 22px; font-weight: 700; color: var(--brand-orange);
  }
  .card-back .address {
    position: absolute; right: 28px; top: 196px;
    text-align: right; font-size: 15px; line-height: 21px; color: var(--ink);
  }
</style>
</head>
<body>
<main class="stage">
  <section class="card card-front" aria-label="Card front">
    <div class="social" aria-hidden="true"><span></span><span></span><span></span><span></span></div>
    <div class="wordmark">
      <span class="wordmark-square" aria-hidden="true"></span>
      <span class="wordmark-name">Purrnest Nook Co</span>
    </div>
    <p class="site">www.purrnestnookco.com</p>
  </section>

  <section class="card card-back" aria-label="Card back">
    <div class="person">
      <p class="person-name">Maren Kealoha</p>
      <p class="person-role">CEO/FOUNDER</p>
    </div>
    <ul class="contacts">
      <li><svg viewBox="0 0 10 10"><path d="M2 0h2l1 3-1.5 1a6 6 0 0 0 2.5 2.5L7 5l3 1v2a2 2 0 0 1-2 2A8 8 0 0 1 0 2a2 2 0 0 1 2-2z"/></svg>+1 (808) 571 6023</li>
      <li><svg viewBox="0 0 10 10"><path d="M0 2h10v6H0z"/></svg>support@purrnestnookco.com</li>
      <li><svg viewBox="0 0 10 10"><path d="M5 0a3.5 3.5 0 0 1 3.5 3.5C8.5 6 5 10 5 10S1.5 6 1.5 3.5A3.5 3.5 0 0 1 5 0z"/></svg>www.purrnestnookco.com</li>
    </ul>
    <div class="wordmark">
      <span class="wordmark-dot" aria-hidden="true"></span>
      <span class="wordmark-name">Purrnest Nook Co</span>
    </div>
    <div class="divider"></div>
    <address class="address" style="font-style:normal">4120 Hibiscus Row<br>Honolulu, Hawaii 96815</address>
  </section>
</main>
</body>
</html>
```